Copperleaf Roofing Business Card

This is my current business card. But I’d like to make some changes. Somewhere on the card I’d like to list some of the services we offer. Maybe on the back? But I’d still like to keep the red. White and black modern look.

-residential & commercial roofing
-Roof Repairs & Maintenance
-Storm Damage & Insurance Claims specialist
-Christmas Lights and permanent Christmas lights
Fencing. Windows. Gutters. Siding. Sheetrock, painting.

```html
<!DOCTYPE html>
<html lang="en">
<head>
<meta charset="utf-8">
<title>Copperleaf Roofing Business Card</title>
<link rel="stylesheet" href="https://fonts.googleapis.com/css2?family=Orbitron:wght@700;800&family=Montserrat:wght@400;500&display=swap">
<style>
  :root {
    --red: #e31b23;
    --black: #111111;
    --ink: #1a1a1a;
    --white: #ffffff;
    --backdrop: #8c7257;
  }
  * { margin: 0; padding: 0; box-sizing: border-box; }
  html, body { width: 900px; height: 1200px; overflow: hidden; }
  body { background: var(--backdrop); position: relative; font-family: "Montserrat", sans-serif; color: var(--ink); }

  .card {
    position: absolute;
    background: var(--white);
    border-radius: 22px;
    overflow: hidden;
  }
  .card--front { left: 80px; top: 131px; width: 742px; height: 441px; }
  .card--back  { left: 77px; top: 638px; width: 745px; height: 440px; }

  .edge-bands { position: absolute; left: 0; bottom: 0; width: 100%; height: 20px; }

  .brand-mark { position: absolute; border-radius: 50%; background: var(--red); }
  .brand-name {
    position: absolute;
    font-family: "Orbitron", sans-serif;
    font-weight: 800;
    color: var(--black);
    text-align: center;
    line-height: 1.25;
    letter-spacing: 1px;
  }

  .card--front .brand-mark { left: 528px; top: 37px; width: 124px; height: 124px; }
  .card--front .brand-name { left: 440px; top: 178px; width: 300px; font-size: 23px; }

  .person { position: absolute; left: 33px; top: 203px; }
  .person__name { font-family: "Orbitron", sans-serif; font-weight: 800; font-size: 24px; letter-spacing: 1px; color: var(--black); }
  .person__name span { color: var(--red); }
  .person__role { font-size: 16px; margin-top: 5px; }

  .divider { position: absolute; left: 30px; top: 260px; width: 686px; height: 1px; background: var(--red); }

  .contacts { position: absolute; left: 34px; top: 330px; list-style: none; font-size: 16.5px; }
  .contacts li { display: flex; align-items: center; height: 28px; }
  .contacts svg { width: 15px; height: 15px; margin-right: 9px; fill: var(--red); }

  .services { position: absolute; right: 24px; top: 276px; list-style: none; text-align: right; font-size: 16.5px; line-height: 20px; }
  .services li { position: relative; padding-right: 14px; margin-bottom: 6px; }
  .services li::after {
    content: ""; position: absolute; right: 0; top: 8px;
    width: 6px; height: 6px; border-radius: 50%; background: var(--red);
  }

  .card--back .brand-mark { left: 283px; top: 67px; width: 182px; height: 182px; }
  .card--back .brand-name { left: 0; top: 276px; width: 745px; font-size: 40px; line-height: 1.3; }
</style>
</head>
<body>

<section class="card card--front">
  <div class="brand-mark"></div>
  <div class="brand-name">COPPERLEAF<br>ROOFING CO.</div>

  <div class="person">
    <div class="person__name">DEAN <span>CALLOWAY</span></div>
    <div class="person__role">Owner</div>
  </div>

  <div class="divider"></div>

  <ul class="contacts">
    <li><svg viewBox="0 0 24 24"><path d="M6.6 10.8a15 15 0 0 0 6.6 6.6l2.2-2.2a1 1 0 0 1 1-.25 11.4 11.4 0 0 0 3.6.57 1 1 0 0 1 1 1V20a1 1 0 0 1-1 1A17 17 0 0 1 3 4a1 1 0 0 1 1-1h3.5a1 1 0 0 1 1 1c0 1.25.2 2.45.57 3.57a1 1 0 0 1-.25 1z"/></svg>682-555-0148</li>
    <li><svg viewBox="0 0 24 24"><path d="M2 5h20v14H2z M2 5l10 7 10-7" fill="var(--red)"/><path d="M2 6l10 7 10-7" fill="none" stroke="#fff" stroke-width="1.5"/></svg>dean@copperleafroofing.com</li>
    <li><svg viewBox="0 0 24 24"><circle cx="12" cy="12" r="10"/><path d="M2 12h20M12 2c3 3 3 17 0 20M12 2c-3 3-3 17 0 20" fill="none" stroke="#fff" stroke-width="1.4"/></svg>www.copperleafroofing.com</li>
  </ul>

  <ul class="services">
    <li>residential &amp; commercial roofing</li>
    <li>Roof Repairs &amp; Maintenance</li>
    <li>Storm Damage &amp;<br>Insurance Claims specialist</li>
    <li>Fencing. Windows. Gutters.<br>Siding. Sheetrock, painting</li>
  </ul>

  <svg class="edge-bands" viewBox="0 0 742 20" preserveAspectRatio="none">
    <polygon points="0,0 375,0 355,20 0,20" fill="var(--black)"/>
    <polygon points="383,0 742,0 742,20 363,20" fill="var(--red)"/>
  </svg>
</section>

<section class="card card--back">
  <div class="brand-mark"></div>
  <div class="brand-name">COPPERLEAF<br>ROOFING CO.</div>

  <svg class="edge-bands" viewBox="0 0 745 20" preserveAspectRatio="none">
    <polygon points="0,0 375,0 355,20 0,20" fill="var(--black)"/>
    <polygon points="383,0 745,0 745,20 363,20" fill="var(--red)"/>
  </svg>
</section>

</body>
</html>
```